Playful Website Design Needed Pet Sitting and Dog Walking Business

Need a simple one page Web Design Built on WordPress.
Sections:

About Us
Services Provided
Costs
Contact Us
Intake Form (Questionnaire that goes to email)
See us in Action

Industry/Entity Type

Pet Sitting and Dog Walking

Number of Pages Required

1 page

Font styles to use
Other font styles liked:
• See the Business Card Font and use that.

Colors
EE7325
F08F49
F5BC92
FAE3D3
FDF4ED

Requirements
Must have
• See attached Logo Design, with Font's and Colors Use these as theme guide

```html
<!DOCTYPE html>
<html lang="en">
<head>
<meta charset="utf-8">
<title>Paws Together Care</title>
<link href="https://fonts.googleapis.com/css2?family=Kalam:wght@400;700&family=Roboto:wght@400;500&family=Crimson+Text&display=swap" rel="stylesheet">
<style>
:root{
  --orange:#f15a16;
  --orange-soft:#f08f49;
  --peach:#f5bc92;
  --green:#5fe43a;
  --green-dark:#3fbf22;
  --ink:#111;
  --white:#fff;
  --black:#000;
}
*{margin:0;padding:0;box-sizing:border-box}
html,body{width:1200px;height:3466px;overflow:hidden;background:var(--white)}
body{position:relative;font-family:"Kalam",cursive;color:var(--ink)}
.abs{position:absolute}
.contact-bar{left:457px;top:0;width:743px;height:54px;background:var(--orange);border-bottom-left-radius:50px}
.bar-item{top:10px;height:36px;display:flex;align-items:center;gap:14px;color:var(--white);font-family:"Roboto",sans-serif;font-size:20px}
.bar-icon{width:36px;height:36px;border-radius:50%;background:var(--white);display:flex;align-items:center;justify-content:center}
.brand{display:flex;align-items:center;gap:10px;font-weight:700;color:var(--orange);font-size:26px;line-height:1.05}
.brand-dot{width:34px;height:34px;border-radius:50%;background:var(--orange-soft);flex:none}
.nav{top:78px;display:flex;font-size:18px}
.nav a{position:absolute;white-space:nowrap;color:var(--ink);text-decoration:none}
.nav a.active{color:var(--orange)}
.login{left:983px;top:74px;width:117px;height:40px;border-radius:20px;background:var(--orange);color:var(--white);font-size:20px;display:flex;align-items:center;justify-content:center;letter-spacing:1px}
.hero-title{left:94px;top:278px;color:var(--white);font-size:54px;line-height:78px;font-weight:700;letter-spacing:2px;text-transform:uppercase}
.btn{display:flex;align-items:center;justify-content:center;border-radius:28px;text-transform:uppercase;letter-spacing:1px;font-size:18px}
.btn-light{background:var(--white);color:var(--orange);box-shadow:3px 4px 0 var(--white),4px 5px 0 var(--orange)}
.btn-orange{background:var(--orange);color:var(--white);box-shadow:3px 4px 0 var(--white),4px 6px 0 var(--orange)}
.eyebrow{font-size:22px;text-transform:uppercase;letter-spacing:1px}
.section-title{font-size:38px;color:var(--orange);text-transform:uppercase;letter-spacing:2px;font-weight:700}
.body-text{font-size:16px;line-height:26px}
.services-title{left:0;width:1200px;top:1470px;text-align:center;color:var(--white);font-size:34px;letter-spacing:2px;text-transform:uppercase}
.card{top:1574px;height:379px;border:1.5px solid rgba(255,255,255,.8);border-radius:24px;color:var(--white);text-align:center}
.card.featured{background:var(--orange);border:none}
.card-icon{position:absolute;left:50%;top:40px;width:148px;height:148px;margin-left:-74px;border-radius:50%;background:var(--orange);display:flex;align-items:center;justify-content:center}
.featured .card-icon{background:var(--white)}
.card h3{position:absolute;left:10px;right:10px;top:210px;font-size:22px;font-weight:400;text-transform:uppercase;line-height:28px}
.card p{position:absolute;left:34px;right:34px;font-size:15px;line-height:25px}
.footer-heading{left:101px;top:2745px;color:var(--white);font-size:32px;line-height:48px;text-transform:uppercase;letter-spacing:1px}
.f-item{left:101px;display:flex;align-items:center;gap:14px;color:var(--white);font-family:"Roboto",sans-serif;font-size:15px;line-height:24px}
.f-icon{width:36px;height:36px;border-radius:50%;background:var(--white);display:flex;align-items:center;justify-content:center;flex:none}
.directions{left:107px;top:3090px;color:var(--white);font-family:"Crimson Text",serif;font-size:17px;line-height:24px}
.social-row{left:106px;top:3128px;display:flex;gap:12px}
.social{width:30px;height:30px;border-radius:50%;background:var(--white);display:flex;align-items:center;justify-content:center}
.social span{width:10px;height:10px;border-radius:50%;background:var(--black)}
.form-panel{left:459px;top:2670px;width:641px;height:515px;background:var(--orange);border-radius:14px}
.form-title{left:506px;top:2700px;color:var(--white);font-size:30px;text-transform:uppercase;letter-spacing:1px}
.field{background:var(--white);border-radius:26px;font-size:13px;color:#555;text-transform:uppercase;padding:14px 24px;letter-spacing:1px}
.foot-nav a{position:absolute;top:3264px;color:var(--white);font-size:19px;text-decoration:none;white-space:nowrap}
.copyright{left:0;width:1200px;top:3386px;text-align:center;color:var(--white);font-family:"Crimson Text",serif;font-size:16px}
</style>
</head>
<body>

<!-- Header -->
<div class="abs contact-bar"></div>
<div class="abs bar-item" style="left:522px">
  <span class="bar-icon"><svg width="18" height="18" viewBox="0 0 24 24"><path fill="#f15a16" d="M6.6 10.8a15 15 0 0 0 6.6 6.6l2.2-2.2c.3-.3.7-.4 1-.2 1.1.4 2.3.6 3.6.6.6 0 1 .4 1 1V20c0 .6-.4 1-1 1A17 17 0 0 1 3 4c0-.6.4-1 1-1h3.5c.6 0 1 .4 1 1 0 1.3.2 2.5.6 3.6.1.3 0 .7-.2 1z"/></svg></span>
  +1 555-014-2290
</div>
<div class="abs bar-item" style="left:771px">
  <span class="bar-icon"><svg width="20" height="16" viewBox="0 0 24 18"><rect x="1" y="1" width="22" height="16" rx="2" fill="none" stroke="#f15a16" stroke-width="2"/><path d="M2 3l10 7 10-7" fill="none" stroke="#f15a16" stroke-width="2"/></svg></span>
  hello@pawstogethercare.com
</div>
<div class="abs brand" style="left:97px;top:34px"><span class="brand-dot"></span><span>Paws Together<br>Care</span></div>
<nav class="abs nav">
  <a class="active" style="left:315px">Home</a>
  <a style="left:390px">About Us</a>
  <a style="left:495px">Services Provided</a>
  <a style="left:667px">Costs</a>
  <a style="left:740px">Contact Us</a>
  <a style="left:864px">Contact form</a>
</nav>
<div class="abs login">LOGIN</div>

<!-- Hero -->
<svg class="abs" style="left:0;top:133px" width="1200" height="680" viewBox="0 0 1200 680" role="img" aria-label="Smiling woman sitting on a park bench with three dogs, blended into orange">
  <defs>
    <linearGradient id="heroGrad" x1="0" x2="1" y1="0" y2="0">
      <stop offset="0" stop-color="#f26a1b"/>
      <stop offset=".45" stop-color="#ef7d2f"/>
      <stop offset=".7" stop-color="#7aa04a"/>
      <stop offset="1" stop-color="#5d9a3a"/>
    </linearGradient>
  </defs>
  <path d="M0 0H1200V590C1120 560 1040 570 900 580 720 590 600 660 420 665 250 670 120 640 0 610Z" fill="url(#heroGrad)"/>
</svg>
<div class="abs hero-title">Welcome to<br>Paws Together<br>Care</div>
<div class="abs btn btn-light" style="left:98px;top:545px;width:227px;height:64px">Get Started</div>

<!-- About -->
<svg class="abs" style="left:0;top:840px" width="660" height="550" viewBox="0 0 660 550" role="img" aria-label="Two dog walkers with several dogs on leads in a park">
  <path d="M180 80C260 30 400 0 520 70 600 120 590 260 520 330 460 390 360 380 250 420 150 460 60 400 40 320 20 230 100 130 180 80Z" fill="none" stroke="#f15a16" stroke-width="2"/>
  <path d="M200 100C280 50 420 40 520 110 590 160 600 280 560 330 500 400 380 420 290 450 190 480 20 470 0 420V80C60 60 130 140 200 100Z" fill="#6f8c4a"/>
  <path d="M0 100C60 60 140 90 170 160 200 260 190 380 140 460 100 520 30 510 0 480Z" fill="#c8473c"/>
</svg>
<div class="abs eyebrow" style="left:646px;top:875px">About us</div>
<div class="abs section-title" style="left:642px;top:912px">Paws Together Care</div>
<p class="abs body-text" style="left:646px;top:976px;width:460px">Sed ut perspiciatis unde omnis iste natus error sit voluptatem accusantium doloremque laudantium, totam rem aperiam, eaque ipsa quae ab illo inventore veritatis et quasi architecto beatae vitae dicta sunt explicabo. Nemo enim ipsam voluptatem quia voluptas sit aspernatur aut odit aut fugit, sed quia consequuntur magni dolores eos qui ratione voluptatem sequi nesciunt. magnam aliquam quaerat voluptatem.</p>
<div class="abs btn btn-orange" style="left:648px;top:1183px;width:183px;height:50px">Read More</div>

<!-- Services -->
<svg class="abs" style="left:0;top:1320px" width="1200" height="780" viewBox="0 0 1200 780" role="img" aria-label="Green tinted background photo of dogs">
  <path d="M0 75C140 60 260 75 420 55 600 30 800 50 960 30 1070 15 1150 10 1200 30V730C1120 690 1000 700 840 715 600 740 360 700 180 735 90 755 30 770 0 770Z" fill="var(--green)"/>
  <path d="M0 80C140 62 260 78 420 58 600 33 800 52 960 33" fill="none" stroke="#f15a16" stroke-width="2"/>
</svg>
<div class="abs services-title">Services Provided</div>

<div class="abs card" style="left:101px;width:317px">
  <div class="card-icon"><svg width="80" height="80" viewBox="0 0 24 24"><g fill="#fff"><ellipse cx="12" cy="16" rx="5.5" ry="4.5"/><circle cx="5" cy="10" r="2.3"/><circle cx="9" cy="5.5" r="2.3"/><circle cx="15" cy="5.5" r="2.3"/><circle cx="19" cy="10" r="2.3"/></g></svg></div>
  <h3>We Feed</h3>
  <p style="top:248px">Excepteur sint occaecat cupidatat non proident, sunt in culpa qui officia deserunt mollit</p>
</div>
<div class="abs card featured" style="left:441px;width:319px">
  <div class="card-icon"><svg width="70" height="70" viewBox="0 0 24 24"><g fill="#111"><circle cx="15" cy="4" r="2.5"/><path d="M12 8h5l2 8h-3l-1 5h-3l1-6-2-2-2 2H7z"/><circle cx="5" cy="11" r="1.6"/><path d="M3 13h5l1 8H7l-1-4-2 4H2l1-5z"/></g></svg></div>
  <h3 style="top:200px">Walk and play with<br>your pet</h3>
  <p style="top:262px">Excepteur sint occaecat cupidatat non proident, sunt in culpa qui officia deserunt mollit</p>
</div>
<div class="abs card" style="left:781px;width:318px">
  <div class="card-icon"><svg width="70" height="70" viewBox="0 0 24 24"><path d="M12 2a7 7 0 0 0-7 7c0 5 7 12 7 12s7-7 7-12a7 7 0 0 0-7-7z" fill="none" stroke="#fff" stroke-width="1.6"/><g fill="#fff"><ellipse cx="12" cy="11" rx="2.3" ry="1.9"/><circle cx="9.3" cy="8.3" r=".9"/><circle cx="11" cy="6.8" r=".9"/><circle cx="13" cy="6.8" r=".9"/><circle cx="14.7" cy="8.3" r=".9"/></g><ellipse cx="12" cy="22" rx="5" ry="1" fill="none" stroke="#fff"/></svg></div>
  <h3>Each Visit</h3>
  <p style="top:248px">Excepteur sint occaecat cupidatat non proident, sunt in culpa qui officia deserunt mollit</p>
</div>

<!-- Costs -->
<div class="abs eyebrow" style="left:100px;top:2195px">Costs</div>
<div class="abs section-title" style="left:98px;top:2232px">Paws Together Care</div>
<p class="abs body-text" style="left:101px;top:2295px;width:460px">Sed ut perspiciatis unde omnis iste natus error sit voluptatem accusantium doloremque laudantium, totam rem aperiam, eaque ipsa quae ab illo inventore veritatis et quasi architecto beatae vitae dicta sunt explicabo. Nemo enim ipsam voluptatem quia voluptas sit aspernatur aut odit aut fugit, sed quia consequuntur magni dolores eos qui ratione voluptatem sequi nesciunt. magnam aliquam quaerat voluptatem.</p>
<div class="abs btn btn-orange" style="left:104px;top:2502px;width:182px;height:51px">Read More</div>
<svg class="abs" style="left:590px;top:2125px" width="520" height="460" viewBox="0 0 520 460" role="img" aria-label="Boy walking a white fluffy dog on a lead through a grassy field">
  <path d="M220 10C360 0 500 60 510 200 518 320 420 440 280 440 180 440 110 390 100 330" fill="none" stroke="#f15a16" stroke-width="2"/>
  <path d="M150 20C280 -10 440 40 470 150 500 260 400 380 280 410 160 440 30 380 5 260 -15 150 50 45 150 20Z" fill="#7f9a5a"/>
  <path d="M10 270C120 300 300 300 460 250 440 330 370 400 280 415 160 440 50 380 10 270Z" fill="#b9b07a"/>
</svg>

<!-- Footer -->
<svg class="abs" style="left:0;top:2660px" width="1200" height="806" viewBox="0 0 1200 806">
  <path d="M0 80C120 30 300 40 470 75L1100 70C1150 60 1180 45 1200 35V806H0Z" fill="var(--black)"/>
  <path d="M0 80C120 30 300 40 470 75" fill="none" stroke="#f15a16" stroke-width="6"/>
  <path d="M1100 72C1150 62 1180 48 1200 38" fill="none" stroke="#f15a16" stroke-width="6"/>
</svg>
<div class="abs footer-heading">Contact us<br>today</div>
<div class="abs f-item" style="top:2858px">
  <span class="f-icon"><svg width="14" height="18" viewBox="0 0 14 20"><path d="M7 0a7 7 0 0 0-7 7c0 5 7 13 7 13s7-8 7-13a7 7 0 0 0-7-7z" fill="#f15a16"/><circle cx="7" cy="7" r="2.5" fill="#fff"/></svg></span>
  <span>Lorem ipsum dolor sit amet,<br>consectetur adipiscing</span>
</div>
<div class="abs f-item" style="top:2959px">
  <span class="f-icon"><svg width="16" height="12" viewBox="0 0 24 18"><rect width="24" height="18" rx="2" fill="#f15a16"/><path d="M1 2l11 8 11-8" fill="none" stroke="#fff" stroke-width="2"/></svg></span>
  <span>hello@pawstogethercare.com</span>
</div>
<div class="abs f-item" style="top:3026px">
  <span class="f-icon"><svg width="16" height="16" viewBox="0 0 24 24"><path fill="#f15a16" d="M6.6 10.8a15 15 0 0 0 6.6 6.6l2.2-2.2c.3-.3.7-.4 1-.2 1.1.4 2.3.6 3.6.6.6 0 1 .4 1 1V20c0 .6-.4 1-1 1A17 17 0 0 1 3 4c0-.6.4-1 1-1h3.5c.6 0 1 .4 1 1 0 1.3.2 2.5.6 3.6.1.3 0 .7-.2 1z"/></svg></span>
  <span>+1 555-014-2290</span>
</div>
<div class="abs directions">GET DIRECTIONS</div>
<div class="abs social-row">
  <span class="social" role="img" aria-label="Social profile link"><span></span></span>
  <span class="social" role="img" aria-label="Social profile link"><span></span></span>
  <span class="social" role="img" aria-label="Social profile link"><span></span></span>
  <span class="social" role="img" aria-label="Social profile link"><span></span></span>
</div>

<div class="abs form-panel"></div>
<div class="abs form-title">Contact From</div>
<div class="abs field" style="left:499px;top:2757px;width:269px;height:51px">First Name*</div>
<div class="abs field" style="left:790px;top:2757px;width:270px;height:51px">Last Name*</div>
<div class="abs field" style="left:499px;top:2824px;width:269px;height:52px">Email*</div>
<div class="abs field" style="left:790px;top:2824px;width:270px;height:52px">Phone*</div>
<div class="abs field" style="left:499px;top:2899px;width:561px;height:176px;border-radius:30px">Tell me about your case*</div>
<div class="abs btn btn-light" style="left:682px;top:3098px;width:180px;height:50px;font-size:17px">Send Now</div>

<div class="abs brand" style="left:106px;top:3250px"><span class="brand-dot"></span><span>Paws Together<br>Care</span></div>
<nav class="foot-nav">
  <a style="left:387px">Home</a>
  <a style="left:468px">About Us</a>
  <a style="left:582px">Services Provided</a>
  <a style="left:769px">Costs</a>
  <a style="left:849px">Contact Us</a>
  <a style="left:985px">Contact form</a>
</nav>
<div class="abs" style="left:97px;top:3360px;width:1003px;border-top:1.5px dashed #888"></div>
<div class="abs copyright">© copyrights 2022 pawstogethercare | All Rights Reserved</div>

</body>
</html>
```